High-Converting Facebook Ads for Portals Drapes & Louvres (6 Products)

We are looking for a graphic designer to create high-quality Facebook & Instagram ads for our business: Portals Drapes and Louvres (Melbourne, Australia).

We require 6 separate ad designs, each for a different product:

Zipscreen Blinds

Outdoor Awnings

Plantation Shutters

Roller Shutters

Security Doors

Roller Blinds & Sheer Curtains

Ad Specifications:

Sizes:

1440 x 1800 px (4:5 ratio)

1080 x 1080 px (1:1 ratio)

1080 x 1920 px (9:16 ratio for Stories/Reels)

Format: PNG (high resolution, not blurry)

Designed specifically for Meta (Facebook/Instagram ads)

Mobile-friendly layout (clear, easy to read)

Style:

Bold, sales-driven, retail-style ads (NOT minimal)

Eye-catching and designed to generate leads

Clean, professional layout

Similar to promotional home improvement ads

Brand Colours:

Red: #E31E24

Blue: #0072BC

White backgrounds

Each ad must include:

“SALE NOW ON” banner at top

Our showroom address:
482 Upper Wattleby Road, Kestrel Heights (must be fully visible, not cut off)

Phone number: 9471 2658

Our logo (provided)

Badge: “Celebrating 13 YEARS in Business” (must be clean and readable)

Call to Action:

For 5 ads: “Book a FREE quote TODAY!”

For Security Doors ad: “ORDER NOW”

Offers / Pricing:

Most products: “UP TO 40% OFF”

Plantation Shutters: “FROM $299/sqm”

Security Doors: “FROM $750”

Content for each ad (examples):

Zipscreen Blinds:

Made to Measure

Fully Installed

Wind, Sun & Insect Protection

Outdoor Awnings:

Reduce Heat & Glare

Energy Saving

Custom Made

Plantation Shutters:

Modern & Elegant

Light & Privacy Control

Durable & Easy Care

Roller Shutters:

Security Protection

Block Heat & Noise

Total Light Control

Security Doors:

3 Point Locking

Premium Mesh

Custom Made

Blinds & Sheers:

Huge Range of Fabrics

Modern Soft Finish

Perfect for Any Room

Important Notes:

All text must be sharp and easy to read (no blur)

Layout must be balanced and not overcrowded

Ensure no text is cut off (especially address and headings)

Badge text must be straight and professional (no distortion)

Use high-quality, relevant images (we will provide references)

Goal:
Create ads that look professional, trustworthy, and generate enquiries/bookings for in-home quotes.

We are open to creative ideas but want a strong, bold retail-style ad that converts.
I have uploaed chatgpt mocks

Target Market(s)

Homeowners in Melbourne, Australia (typically aged 30–65) looking to improve their homes with blinds, shutters, awnings and security doors. Mid to high income households focused on quality, security, and modern home upgrades.

Industry/Entity Type

Home Improvement / Construction / Retail

Font styles to use
Sans Serif

Requirements
Must have
• Clear, bold and easy-to-read text (must be readable on mobile) High-quality, non-blurry design Strong “SALE” style layout (retail promotional look) Proper spacing (no overcrowded designs) All key info visible (address must NOT be cut off) Correct pricing and offers included Clean “13 YEARS” badge (no distortion or curved text) Consistent branding across all 6 ads
Nice to have
• Modern, slightly premium feel while still being bold Good use of contrast (red/blue/white) Subtle shadows or layering to improve depth Clean use of icons or bullet points Strong hierarchy (headline → benefits → offer → CTA) Variations in layout for testing different ad styles
Should not have
• Minimal or plain designs (we want bold, sales-driven ads) Hard-to-read fonts or script fonts Low-quality or blurry images Overcrowded layouts with too much text Important text cut off (especially address or headings) Overuse of effects or “cheap” looking graphics Yellow-heavy colour schemes (must follow brand colours)

```html
<!DOCTYPE html>
<html lang="en">
<head>
<meta charset="utf-8">
<title>Portals Drapes &amp; Louvres – Sale Ad Set</title>
<link rel="stylesheet" href="https://fonts.googleapis.com/css2?family=Anton&family=Archivo+Black&family=Montserrat:wght@500;700;800&display=swap">
<style>
  :root{
    --red:#e31e24;
    --blue:#0072bc;
    --white:#ffffff;
    --ink:#1d1d1f;
    --rule:#d9dde2;
    --board:#0b1d2c;
    --label:#7fb1e3;
    --display:'Archivo Black', 'Arial Black', sans-serif;
    --condensed:'Anton', 'Impact', sans-serif;
    --body:'Montserrat', 'Arial', sans-serif;
  }
  *{box-sizing:border-box;margin:0;padding:0}
  html,body{width:1200px;height:2424px;overflow:hidden;background:var(--board)}
  .board{position:relative;width:1200px;height:2424px}
  .sprites{position:absolute;width:0;height:0;overflow:hidden}

  .row{position:absolute;left:0;width:1200px;height:360px}
  .size-label{position:absolute;top:338px;font:500 14px/1 var(--body);color:var(--label);letter-spacing:.3px}
  .size-label--feed{left:109px}
  .size-label--story{left:491px}
  .size-label--square{left:785px}

  /* ---------- ad shell ---------- */
  .ad{position:absolute;top:0;height:319px;background:var(--white);overflow:hidden}
  .ad--feed{left:109px;width:256px}
  .ad--story{left:491px;width:180px}
  .ad--square{left:785px;width:320px}
  .ad > *{position:absolute}

  /* headline */
  .sale{color:var(--red);line-height:1}
  .sale span{display:block;white-space:nowrap}
  .ad--feed .sale{left:18px;top:19px;font-family:var(--display)}
  .ad--feed .sale__big{font-size:37px;line-height:32px;letter-spacing:5px}
  .ad--feed .sale__small{font-size:25px;line-height:22px;letter-spacing:1px}
  .ad--story .sale{left:0;width:180px;top:68px;text-align:center;font-family:var(--display)}
  .ad--story .sale__big{font-size:45px;line-height:38px;letter-spacing:5px;padding-left:5px}
  .ad--story .sale__small{font-size:30px;line-height:24px;letter-spacing:2px}
  .ad--square .sale{left:24px;top:20px;font-family:var(--condensed);font-size:42px;letter-spacing:-.3px}
  .ad--square .sale span{display:inline}

  /* brand */
  .brand{display:flex;align-items:center;gap:4px}
  .brand__mark{flex:none;background:var(--red)}
  .brand__name{font-family:var(--body);font-weight:800;color:var(--blue);text-transform:uppercase;line-height:1.1}
  .ad--feed .brand{left:166px;top:30px;width:80px}
  .ad--feed .brand__mark{width:11px;height:11px}
  .ad--feed .brand__name{font-size:8px}
  .ad--story .brand{left:0;width:180px;top:26px;justify-content:center}
  .ad--story .brand__mark{width:14px;height:14px}
  .ad--story .brand__name{font-size:9px}
  .ad--square .brand{left:232px;top:28px;width:78px}
  .ad--square .brand__mark{width:11px;height:11px}
  .ad--square .brand__name{font-size:8px}

  /* showroom pill */
  .address{display:flex;border-radius:99px;overflow:hidden;font-family:var(--body);font-weight:700;color:var(--white);white-space:nowrap}
  .address span{display:flex;align-items:center}
  .address__label{background:var(--red);padding:0 .9em}
  .address__text{background:var(--blue);flex:1;padding:0 .7em}
  .ad--feed .address{left:13px;top:80px;width:235px;height:14px;font-size:5.8px}
  .ad--story .address{left:10px;top:140px;width:160px;height:11px;font-size:4.2px}
  .ad--square .address{left:18px;top:71px;width:286px;height:15px;font-size:7px}

  /* bands */
  .cta-band{left:0;width:100%;background:var(--red);color:var(--white);font-family:var(--condensed);white-space:nowrap}
  .cta-band--order{font-family:var(--display);letter-spacing:2px}
  .ad--feed .cta-band{top:232px;height:25px;padding-left:91px;font-size:15px;line-height:25px}
  .ad--feed .cta-band--order{font-size:15px}
  .ad--story .cta-band{top:259px;height:17px;padding-left:64px;font-size:10.5px;line-height:17px}
  .ad--story .cta-band--order{font-size:10px;letter-spacing:1px}
  .ad--square .cta-band{top:238px;height:26px;padding-left:118px;font-size:18px;line-height:26px}
  .ad--square .cta-band--order{font-size:17px;letter-spacing:3px}

  .contact-band{left:0;width:100%;bottom:0;background:var(--blue);color:var(--white)}
  .contact-band > *{position:absolute}
  .phone{display:flex;align-items:center;font-family:var(--display);line-height:1;white-space:nowrap}
  .phone svg{flex:none}
  .web{font-family:var(--body);font-weight:800;white-space:nowrap}
  .ad--feed .contact-band{height:62px}
  .ad--feed .phone{left:92px;top:5px;font-size:18px;gap:5px}
  .ad--feed .phone svg{width:12px;height:12px}
  .ad--feed .web{left:0;width:100%;text-align:center;top:34px;font-size:10.3px}
  .ad--story .contact-band{height:43px}
  .ad--story .phone{left:64px;top:3px;font-size:13px;gap:4px}
  .ad--story .phone svg{width:10px;height:10px}
  .ad--story .web{left:0;width:100%;text-align:center;top:25px;font-size:6.6px}
  .ad--square .contact-band{height:55px}
  .ad--square .phone{left:118px;top:3px;font-size:21px;gap:6px}
  .ad--square .phone svg{width:15px;height:15px}
  .ad--square .web{left:120px;top:31px;font-size:9.6px}

  /* product imagery */
  .photo{background:#ccc}
  .photo--sheers{background:linear-gradient(90deg,#cfcfcb 0%,#f4f3f0 35%,#dcdbd6 60%,#b9b7b0 100%)}
  .photo--roller{background:linear-gradient(90deg,#8a6a55 0%,#8a6a55 12%,#3c4045 12%,#5b6066 60%,#2f3236 100%)}
  .photo--zip{background:linear-gradient(90deg,#d5d7da 0%,#9c5a3c 22%,#a8613f 45%,#26282b 46%,#303336 100%)}
  .photo--awning{background:linear-gradient(180deg,#86a9cb 0%,#262626 28%,#3a3a3a 38%,#6f7d52 60%,#8d8a82 100%)}
  .photo--door{background:linear-gradient(90deg,#161616 0%,#161616 10%,#d6d6d6 20%,#f1f1f1 45%,#cdb57a 62%,#e2e2e2 80%,#161616 90%)}
  .photo--plantation{background:linear-gradient(90deg,#8f918e 0%,#e4e4e1 30%,#f3f3f1 55%,#b6b7b3 100%)}
  .ad--feed .photo{left:15px;top:111px;width:68px;height:143px}
  .ad--story .photo{left:14px;top:160px;width:45px;height:112px}
  .ad--square .photo{left:23px;top:102px;width:81px;height:206px}

  /* product title */
  .product{font-family:var(--condensed);font-weight:400;color:var(--red);text-transform:uppercase;white-space:nowrap}
  .ad--feed .product{left:88px;top:112px;font-size:25px;line-height:27px}
  .ad--story .product{left:64px;top:159px;font-size:27px;line-height:28px}
  .ad--square .product{left:115px;top:100px;font-size:33px;line-height:31px}
  .ad--feed .product--right{left:auto;right:76px;text-align:right}
  .ad--story .product--right{left:auto;right:8px;text-align:right}
  .ad--square .product--right{left:auto;right:87px;text-align:right}
  .ad--feed .product--small{font-size:21px;line-height:24px;top:115px}
  .ad--story .product--small{font-size:23px;line-height:27px;top:161px}
  .ad--square .product--small{font-size:28px;line-height:30px;top:104px}

  /* anniversary badge */
  .ad--feed .badge{left:182px;top:108px;width:58px;height:58px}
  .ad--story .badge{left:15px;top:249px;width:42px;height:42px}
  .ad--square .badge{left:235px;top:97px;width:72px;height:72px}

  /* offer tag */
  .offer{display:flex;flex-direction:column;border-radius:3px;overflow:hidden;box-shadow:0 1px 3px rgba(0,0,0,.25)}
  .offer__top{background:var(--red);color:var(--white);font-family:var(--body);font-weight:500;text-align:left;padding-left:4px;line-height:1}
  .offer__value{flex:1;background:var(--blue);color:var(--white);display:flex;align-items:center;padding-left:4px;font-family:var(--condensed);line-height:1}
  .offer__unit{display:flex;flex-direction:column;font-family:var(--body);font-weight:800;line-height:1;margin-left:1px}
  .offer__cur{font-family:var(--body);font-weight:700;align-self:flex-start;margin-top:.35em}
  .offer__per{font-family:var(--body);font-weight:700;align-self:flex-end;margin-bottom:.7em;margin-left:1px}
  .ad--feed .offer{left:91px;top:177px;width:46px;height:40px}
  .ad--feed .offer__top{font-size:9px;padding-top:1px;height:11px}
  .ad--feed .offer__num{font-size:22px}
  .ad--feed .offer__unit b:first-child{font-size:9px}
  .ad--feed .offer__unit b:last-child{font-size:5.5px}
  .ad--feed .offer__cur{font-size:8px}
  .ad--feed .offer__per{font-size:4px}
  .ad--story .offer{left:66px;top:222px;width:34px;height:26px}
  .ad--story .offer__top{font-size:6px;height:8px;padding-top:1px}
  .ad--story .offer__num{font-size:15px}
  .ad--story .offer__unit b:first-child{font-size:6px}
  .ad--story .offer__unit b:last-child{font-size:4px}
  .ad--story .offer__cur{font-size:6px}
  .ad--story .offer__per{font-size:3px}
  .ad--square .offer{left:120px;top:177px;width:62px;height:52px}
  .ad--square .offer__top{font-size:12px;height:15px;padding-top:1.5px;padding-left:6px}
  .ad--square .offer__value{padding-left:6px}
  .ad--square .offer__num{font-size:29px}
  .ad--square .offer__unit b:first-child{font-size:12px}
  .ad--square .offer__unit b:last-child{font-size:7px}
  .ad--square .offer__cur{font-size:11px}
  .ad--square .offer__per{font-size:5px}

  /* benefit list */
  .benefits{list-style:none;font-family:var(--body);font-weight:800;color:var(--ink);text-transform:uppercase}
  .benefits li{position:relative;border-bottom:1px solid var(--rule)}
  .benefits li::before{content:"";position:absolute;left:0;border:1px solid var(--red);border-radius:50%}
  .ad--feed .benefits{left:140px;top:180px;width:108px;font-size:6.2px;line-height:1.25}
  .ad--feed .benefits li{padding:1.5px 0 1.5px 8px}
  .ad--feed .benefits li::before{top:3px;width:5px;height:5px}
  .ad--story .benefits{left:102px;top:223px;width:70px;font-size:4.3px;line-height:1.25}
  .ad--story .benefits li{padding:1px 0 1px 6px}
  .ad--story .benefits li::before{top:1.8px;width:3.5px;height:3.5px}
  .ad--square .benefits{left:180px;top:181px;width:130px;font-size:8px;line-height:1.25}
  .ad--square .benefits li{padding:2px 0 2px 10px}
  .ad--square .benefits li::before{top:3.5px;width:6px;height:6px}
</style>
</head>
<body>
<main class="board">

<svg class="sprites" aria-hidden="true" focusable="false">
  <symbol id="anniversary-badge" viewBox="0 0 100 100">
    <path id="badge-arc-top" d="M 14 50 A 36 36 0 0 1 86 50" fill="none"/>
    <path id="badge-arc-bottom" d="M 7 50 A 43 43 0 0 0 93 50" fill="none"/>
    <circle cx="50" cy="50" r="48" fill="#e31e24" stroke="#ffffff" stroke-width="2.5"/>
    <circle cx="50" cy="50" r="30" fill="#ffffff"/>
    <circle cx="50" cy="50" r="26" fill="#0072bc"/>
    <text font-family="Montserrat, Arial, sans-serif" font-weight="800" font-size="10.5" fill="#ffffff" letter-spacing="1">
      <textPath href="#badge-arc-top" startOffset="50%" text-anchor="middle">CELEBRATING</textPath>
    </text>
    <text font-family="Montserrat, Arial, sans-serif" font-weight="800" font-size="10.5" fill="#ffffff" letter-spacing="1">
      <textPath href="#badge-arc-bottom" startOffset="50%" text-anchor="middle">IN BUSINESS</textPath>
    </text>
    <text x="50" y="56" text-anchor="middle" font-family="'Archivo Black', Arial, sans-serif" font-size="22" fill="#ffffff">13</text>
    <text x="50" y="67" text-anchor="middle" font-family="Montserrat, Arial, sans-serif" font-weight="700" font-size="6.5" fill="#ffffff" letter-spacing=".5">YEARS</text>
  </symbol>
  <symbol id="phone-icon" viewBox="0 0 24 24">
    <circle cx="12" cy="12" r="12" fill="#e31e24"/>
    <path d="M8.4 5.6l2.1.3 1 3-1.5 1.3a9 9 0 0 0 3.8 3.8l1.3-1.5 3 1 .3 2.1c0 .8-.7 1.5-1.5 1.5A11.4 11.4 0 0 1 6.9 7.1c0-.8.7-1.5 1.5-1.5z" fill="#ffffff"/>
  </symbol>
</svg>

<!-- ================= Blinds & Sheers ================= -->
<section class="row" style="top:118px">
  <article class="ad ad--feed">
    <p class="sale"><span class="sale__big">SALE</span><span class="sale__small">NOW ON</span></p>
    <div class="brand"><span class="brand__mark"></span><span class="brand__name">Portals Drapes &amp; Louvres</span></div>
    <p class="address"><span class="address__label">Showroom address</span><span class="address__text">482 Upper Wattleby Road, Kestrel Heights</span></p>
    <div class="cta-band">BOOK A FREE QUOTE TODAY!</div>
    <div class="contact-band"><p class="phone"><svg><use href="#phone-icon"/></svg>9471 2658</p><p class="web">www.portalsdrapesandlouvres.com.au</p></div>
    <div class="photo photo--sheers" role="img" aria-label="Photo of sheer curtains over a window in a bright living room"></div>
    <h2 class="product">Blinds &amp;<br>Sheers</h2>
    <svg class="badge" role="img" aria-label="Celebrating 13 years in business"><use href="#anniversary-badge"/></svg>
    <div class="offer"><span class="offer__top">UP TO</span><span class="offer__value"><span class="offer__num">40</span><span class="offer__unit"><b>%</b><b>OFF</b></span></span></div>
    <ul class="benefits"><li>Huge range of fabrics</li><li>Modern soft finish</li><li>Perfect for any room</li></ul>
  </article>
  <article class="ad ad--story">
    <div class="brand"><span class="brand__mark"></span><span class="brand__name">Portals Drapes &amp; Louvres</span></div>
    <p class="sale"><span class="sale__big">SALE</span><span class="sale__small">NOW ON</span></p>
    <p class="address"><span class="address__label">Showroom address</span><span class="address__text">482 Upper Wattleby Road, Kestrel Heights</span></p>
    <div class="cta-band">BOOK A FREE QUOTE TODAY!</div>
    <div class="contact-band"><p class="phone"><svg><use href="#phone-icon"/></svg>9471 2658</p><p class="web">www.portalsdrapesandlouvres.com.au</p></div>
    <div class="photo photo--sheers" role="img" aria-label="Photo of sheer curtains over a window in a bright living room"></div>
    <h2 class="product">Blinds &amp;<br>Sheers</h2>
    <div class="offer"><span class="offer__top">UP TO</span><span class="offer__value"><span class="offer__num">40</span><span class="offer__unit"><b>%</b><b>OFF</b></span></span></div>
    <ul class="benefits"><li>Huge range of fabrics</li><li>Modern soft finish</li><li>Perfect for any room</li></ul>
    <svg class="badge" role="img" aria-label="Celebrating 13 years in business"><use href="#anniversary-badge"/></svg>
  </article>
  <article class="ad ad--square">
    <p class="sale"><span>SALE NOW ON</span></p>
    <div class="brand"><span class="brand__mark"></span><span class="brand__name">Portals Drapes &amp; Louvres</span></div>
    <p class="address"><span class="address__label">Showroom address</span><span class="address__text">482 Upper Wattleby Road, Kestrel Heights</span></p>
    <div class="cta-band">BOOK A FREE QUOTE TODAY!</div>
    <div class="contact-band"><p class="phone"><svg><use href="#phone-icon"/></svg>9471 2658</p><p class="web">www.portalsdrapesandlouvres.com.au</p></div>
    <div class="photo photo--sheers" role="img" aria-label="Photo of sheer curtains over a window in a bright living room"></div>
    <h2 class="product">Blinds &amp;<br>Sheers</h2>
    <svg class="badge" role="img" aria-label="Celebrating 13 years in business"><use href="#anniversary-badge"/></svg>
    <div class="offer"><span class="offer__top">UP TO</span><span class="offer__value"><span class="offer__num">40</span><span class="offer__unit"><b>%</b><b>OFF</b></span></span></div>
    <ul class="benefits"><li>Huge range of fabrics</li><li>Modern soft finish</li><li>Perfect for any room</li></ul>
  </article>
  <span class="size-label size-label--feed">1440 X 1800</span>
  <span class="size-label size-label--square">1080 X 1080</span>
</section>

<!-- ================= Roller Shutters ================= -->
<section class="row" style="top:492px">
  <article class="ad ad--feed">
    <p class="sale"><span class="sale__big">SALE</span><span class="sale__small">NOW ON</span></p>
    <div class="brand"><span class="brand__mark"></span><span class="brand__name">Portals Drapes &amp; Louvres</span></div>
    <p class="address"><span class="address__label">Showroom address</span><span class="address__text">482 Upper Wattleby Road, Kestrel Heights</span></p>
    <div class="cta-band">BOOK A FREE QUOTE TODAY!</div>
    <div class="contact-band"><p class="phone"><svg><use href="#phone-icon"/></svg>9471 2658</p><p class="web">www.portalsdrapesandlouvres.com.au</p></div>
    <div class="photo photo--roller" role="img" aria-label="Photo of a grey roller shutter fitted to a brick house window"></div>
    <h2 class="product">Roller<br>Shutters</h2>
    <svg class="badge" role="img" aria-label="Celebrating 13 years in business"><use href="#anniversary-badge"/></svg>
    <div class="offer"><span class="offer__top">UP TO</span><span class="offer__value"><span class="offer__num">40</span><span class="offer__unit"><b>%</b><b>OFF</b></span></span></div>
    <ul class="benefits"><li>Security protection</li><li>Block heat &amp; noise</li><li>Total light control</li></ul>
  </article>
  <article class="ad ad--story">
    <div class="brand"><span class="brand__mark"></span><span class="brand__name">Portals Drapes &amp; Louvres</span></div>
    <p class="sale"><span class="sale__big">SALE</span><span class="sale__small">NOW ON</span></p>
    <p class="address"><span class="address__label">Showroom address</span><span class="address__text">482 Upper Wattleby Road, Kestrel Heights</span></p>
    <div class="cta-band">BOOK A FREE QUOTE TODAY!</div>
    <div class="contact-band"><p class="phone"><svg><use href="#phone-icon"/></svg>9471 2658</p><p class="web">www.portalsdrapesandlouvres.com.au</p></div>
    <div class="photo photo--roller" role="img" aria-label="Photo of a grey roller shutter fitted to a brick house window"></div>
    <h2 class="product">Roller<br>Shutters</h2>
    <div class="offer"><span class="offer__top">UP TO</span><span class="offer__value"><span class="offer__num">40</span><span class="offer__unit"><b>%</b><b>OFF</b></span></span></div>
    <ul class="benefits"><li>Security protection</li><li>Block heat &amp; noise</li><li>Total light control</li></ul>
    <svg class="badge" role="img" aria-label="Celebrating 13 years in business"><use href="#anniversary-badge"/></svg>
  </article>
  <article class="ad ad--square">
    <p class="sale"><span>SALE NOW ON</span></p>
    <div class="brand"><span class="brand__mark"></span><span class="brand__name">Portals Drapes &amp; Louvres</span></div>
    <p class="address"><span class="address__label">Showroom address</span><span class="address__text">482 Upper Wattleby Road, Kestrel Heights</span></p>
    <div class="cta-band">BOOK A FREE QUOTE TODAY!</div>
    <div class="contact-band"><p class="phone"><svg><use href="#phone-icon"/></svg>9471 2658</p><p class="web">www.portalsdrapesandlouvres.com.au</p></div>
    <div class="photo photo--roller" role="img" aria-label="Photo of a grey roller shutter fitted to a brick house window"></div>
    <h2 class="product">Roller<br>Shutters</h2>
    <svg class="badge" role="img" aria-label="Celebrating 13 years in business"><use href="#anniversary-badge"/></svg>
    <div class="offer"><span class="offer__top">UP TO</span><span class="offer__value"><span class="offer__num">40</span><span class="offer__unit"><b>%</b><b>OFF</b></span></span></div>
    <ul class="benefits"><li>Security protection</li><li>Block heat &amp; noise</li><li>Total light control</li></ul>
  </article>
  <span class="size-label size-label--feed">1440 X 1800</span>
  <span class="size-label size-label--square">1080 X 1080</span>
</section>

<!-- ================= Zipscreen Blinds ================= -->
<section class="row" style="top:867px">
  <article class="ad ad--feed">
    <p class="sale"><span class="sale__big">SALE</span><span class="sale__small">NOW ON</span></p>
    <div class="brand"><span class="brand__mark"></span><span class="brand__name">Portals Drapes &amp; Louvres</span></div>
    <p class="address"><span class="address__label">Showroom address</span><span class="address__text">482 Upper Wattleby Road, Kestrel Heights</span></p>
    <div class="cta-band">BOOK A FREE QUOTE TODAY!</div>
    <div class="contact-band"><p class="phone"><svg><use href="#phone-icon"/></svg>9471 2658</p><p class="web">www.portalsdrapesandlouvres.com.au</p></div>
    <div class="photo photo--zip" role="img" aria-label="Photo of a dark zipscreen blind on a brick house"></div>
    <h2 class="product product--right">Zipscreen<br>Blinds</h2>
    <svg class="badge" role="img" aria-label="Celebrating 13 years in business"><use href="#anniversary-badge"/></svg>
    <div class="offer"><span class="offer__top">UP TO</span><span class="offer__value"><span class="offer__num">40</span><span class="offer__unit"><b>%</b><b>OFF</b></span></span></div>
    <ul class="benefits"><li>Made to measure</li><li>Fully installed</li><li>Wind, sun &amp; insect protection</li></ul>
  </article>
  <article class="ad ad--story">
    <div class="brand"><span class="brand__mark"></span><span class="brand__name">Portals Drapes &amp; Louvres</span></div>
    <p class="sale"><span class="sale__big">SALE</span><span class="sale__small">NOW ON</span></p>
    <p class="address"><span class="address__label">Showroom address</span><span class="address__text">482 Upper Wattleby Road, Kestrel Heights</span></p>
    <div class="cta-band">BOOK A FREE QUOTE TODAY!</div>
    <div class="contact-band"><p class="phone"><svg><use href="#phone-icon"/></svg>9471 2658</p><p class="web">www.portalsdrapesandlouvres.com.au</p></div>
    <div class="photo photo--zip" role="img" aria-label="Photo of a dark zipscreen blind on a brick house"></div>
    <h2 class="product product--right">Zipscreen<br>Blinds</h2>
    <div class="offer"><span class="offer__top">UP TO</span><span class="offer__value"><span class="offer__num">40</span><span class="offer__unit"><b>%</b><b>OFF</b></span></span></div>
    <ul class="benefits"><li>Made to measure</li><li>Fully installed</li><li>Wind, sun &amp; insect protection</li></ul>
    <svg class="badge" role="img" aria-label="Celebrating 13 years in business"><use href="#anniversary-badge"/></svg>
  </article>
  <article class="ad ad--square">
    <p class="sale"><span>SALE NOW ON</span></p>
    <div class="brand"><span class="brand__mark"></span><span class="brand__name">Portals Drapes &amp; Louvres</span></div>
    <p class="address"><span class="address__label">Showroom address</span><span class="address__text">482 Upper Wattleby Road, Kestrel Heights</span></p>
    <div class="cta-band">BOOK A FREE QUOTE TODAY!</div>
    <div class="contact-band"><p class="phone"><svg><use href="#phone-icon"/></svg>9471 2658</p><p class="web">www.portalsdrapesandlouvres.com.au</p></div>
    <div class="photo photo--zip" role="img" aria-label="Photo of a dark zipscreen blind on a brick house"></div>
    <h2 class="product product--right">Zipscreen<br>Blinds</h2>
    <svg class="badge" role="img" aria-label="Celebrating 13 years in business"><use href="#anniversary-badge"/></svg>
    <div class="offer"><span class="offer__top">UP TO</span><span class="offer__value"><span class="offer__num">40</span><span class="offer__unit"><b>%</b><b>OFF</b></span></span></div>
    <ul class="benefits"><li>Made to measure</li><li>Fully installed</li><li>Wind, sun &amp; insect protection</li></ul>
  </article>
  <span class="size-label size-label--feed">1440 X 1800</span>
  <span class="size-label size-label--square">1080 X 1080</span>
</section>

<!-- ================= Outdoor Awnings ================= -->
<section class="row" style="top:1240px">
  <article class="ad ad--feed">
    <p class="sale"><span class="sale__big">SALE</span><span class="sale__small">NOW ON</span></p>
    <div class="brand"><span class="brand__mark"></span><span class="brand__name">Portals Drapes &amp; Louvres</span></div>
    <p class="address"><span class="address__label">Showroom address</span><span class="address__text">482 Upper Wattleby Road, Kestrel Heights</span></p>
    <div class="cta-band">BOOK A FREE QUOTE TODAY!</div>
    <div class="contact-band"><p class="phone"><svg><use href="#phone-icon"/></svg>9471 2658</p><p class="web">www.portalsdrapesandlouvres.com.au</p></div>
    <div class="photo photo--awning" role="img" aria-label="Photo of a dark outdoor awning over a patio with garden furniture"></div>
    <h2 class="product">Outdoor<br>Awnings</h2>
    <svg class="badge" role="img" aria-label="Celebrating 13 years in business"><use href="#anniversary-badge"/></svg>
    <div class="offer"><span class="offer__top">UP TO</span><span class="offer__value"><span class="offer__num">40</span><span class="offer__unit"><b>%</b><b>OFF</b></span></span></div>
    <ul class="benefits"><li>Reduce heat &amp; glare</li><li>Energy saving</li><li>Custom made</li></ul>
  </article>
  <article class="ad ad--story">
    <div class="brand"><span class="brand__mark"></span><span class="brand__name">Portals Drapes &amp; Louvres</span></div>
    <p class="sale"><span class="sale__big">SALE</span><span class="sale__small">NOW ON</span></p>
    <p class="address"><span class="address__label">Showroom address</span><span class="address__text">482 Upper Wattleby Road, Kestrel Heights</span></p>
    <div class="cta-band">BOOK A FREE QUOTE TODAY!</div>
    <div class="contact-band"><p class="phone"><svg><use href="#phone-icon"/></svg>9471 2658</p><p class="web">www.portalsdrapesandlouvres.com.au</p></div>
    <div class="photo photo--awning" role="img" aria-label="Photo of a dark outdoor awning over a patio with garden furniture"></div>
    <h2 class="product">Outdoor<br>Awnings</h2>
    <div class="offer"><span class="offer__top">UP TO</span><span class="offer__value"><span class="offer__num">40</span><span class="offer__unit"><b>%</b><b>OFF</b></span></span></div>
    <ul class="benefits"><li>Reduce heat &amp; glare</li><li>Energy saving</li><li>Custom made</li></ul>
    <svg class="badge" role="img" aria-label="Celebrating 13 years in business"><use href="#anniversary-badge"/></svg>
  </article>
  <article class="ad ad--square">
    <p class="sale"><span>SALE NOW ON</span></p>
    <div class="brand"><span class="brand__mark"></span><span class="brand__name">Portals Drapes &amp; Louvres</span></div>
    <p class="address"><span class="address__label">Showroom address</span><span class="address__text">482 Upper Wattleby Road, Kestrel Heights</span></p>
    <div class="cta-band">BOOK A FREE QUOTE TODAY!</div>
    <div class="contact-band"><p class="phone"><svg><use href="#phone-icon"/></svg>9471 2658</p><p class="web">www.portalsdrapesandlouvres.com.au</p></div>
    <div class="photo photo--awning" role="img" aria-label="Photo of a dark outdoor awning over a patio with garden furniture"></div>
    <h2 class="product">Outdoor<br>Awnings</h2>
    <svg class="badge" role="img" aria-label="Celebrating 13 years in business"><use href="#anniversary-badge"/></svg>
    <div class="offer"><span class="offer__top">UP TO</span><span class="offer__value"><span class="offer__num">40</span><span class="offer__unit"><b>%</b><b>OFF</b></span></span></div>
    <ul class="benefits"><li>Reduce heat &amp; glare</li><li>Energy saving</li><li>Custom made</li></ul>
  </article>
  <span class="size-label size-label--feed">1440 X 1800</span>
  <span class="size-label size-label--story">1080 X 1920</span>
  <span class="size-label size-label--square">1080 X 1080</span>
</section>

<!-- ================= Security Doors ================= -->
<section class="row" style="top:1616px">
  <article class="ad ad--feed">
    <p class="sale"><span class="sale__big">SALE</span><span class="sale__small">NOW ON</span></p>
    <div class="brand"><span class="brand__mark"></span><span class="brand__name">Portals Drapes &amp; Louvres</span></div>
    <p class="address"><span class="address__label">Showroom address</span><span class="address__text">482 Upper Wattleby Road, Kestrel Heights</span></p>
    <div class="cta-band cta-band--order">ORDER NOW</div>
    <div class="contact-band"><p class="phone"><svg><use href="#phone-icon"/></svg>9471 2658</p><p class="web">www.portalsdrapesandlouvres.com.au</p></div>
    <div class="photo photo--door" role="img" aria-label="Photo of a black framed decorative security door"></div>
    <h2 class="product">Security<br>Doors</h2>
    <svg class="badge" role="img" aria-label="Celebrating 13 years in business"><use href="#anniversary-badge"/></svg>
    <div class="offer"><span class="offer__top">FROM</span><span class="offer__value"><span class="offer__cur">$</span><span class="offer__num">750</span></span></div>
    <ul class="benefits"><li>3 point locking</li><li>Premium mesh</li><li>Custom made</li></ul>
  </article>
  <article class="ad ad--story">
    <div class="brand"><span class="brand__mark"></span><span class="brand__name">Portals Drapes &amp; Louvres</span></div>
    <p class="sale"><span class="sale__big">SALE</span><span class="sale__small">NOW ON</span></p>
    <p class="address"><span class="address__label">Showroom address</span><span class="address__text">482 Upper Wattleby Road, Kestrel Heights</span></p>
    <div class="cta-band cta-band--order">ORDER NOW</div>
    <div class="contact-band"><p class="phone"><svg><use href="#phone-icon"/></svg>9471 2658</p><p class="web">www.portalsdrapesandlouvres.com.au</p></div>
    <div class="photo photo--door" role="img" aria-label="Photo of a black framed decorative security door"></div>
    <h2 class="product">Security<br>Doors</h2>
    <div class="offer"><span class="offer__top">FROM</span><span class="offer__value"><span class="offer__cur">$</span><span class="offer__num">750</span></span></div>
    <ul class="benefits"><li>3 point locking</li><li>Premium mesh</li><li>Custom made</li></ul>
    <svg class="badge" role="img" aria-label="Celebrating 13 years in business"><use href="#anniversary-badge"/></svg>
  </article>
  <article class="ad ad--square">
    <p class="sale"><span>SALE NOW ON</span></p>
    <div class="brand"><span class="brand__mark"></span><span class="brand__name">Portals Drapes &amp; Louvres</span></div>
    <p class="address"><span class="address__label">Showroom address</span><span class="address__text">482 Upper Wattleby Road, Kestrel Heights</span></p>
    <div class="cta-band cta-band--order">ORDER NOW</div>
    <div class="contact-band"><p class="phone"><svg><use href="#phone-icon"/></svg>9471 2658</p><p class="web">www.portalsdrapesandlouvres.com.au</p></div>
    <div class="photo photo--door" role="img" aria-label="Photo of a black framed decorative security door"></div>
    <h2 class="product">Security<br>Doors</h2>
    <svg class="badge" role="img" aria-label="Celebrating 13 years in business"><use href="#anniversary-badge"/></svg>
    <div class="offer"><span class="offer__top">FROM</span><span class="offer__value"><span class="offer__cur">$</span><span class="offer__num">750</span></span></div>
    <ul class="benefits"><li>3 point locking</li><li>Premium mesh</li><li>Custom made</li></ul>
  </article>
  <span class="size-label size-label--feed">1440 X 1800</span>
  <span class="size-label size-label--story">1080 X 1920</span>
  <span class="size-label size-label--square">1080 X 1080</span>
</section>

<!-- ================= Plantation Shutters ================= -->
<section class="row" style="top:1990px">
  <article class="ad ad--feed">
    <p class="sale"><span class="sale__big">SALE</span><span class="sale__small">NOW ON</span></p>
    <div class="brand"><span class="brand__mark"></span><span class="brand__name">Portals Drapes &amp; Louvres</span></div>
    <p class="address"><span class="address__label">Showroom address</span><span class="address__text">482 Upper Wattleby Road, Kestrel Heights</span></p>
    <div class="cta-band">BOOK A FREE QUOTE TODAY!</div>
    <div class="contact-band"><p class="phone"><svg><use href="#phone-icon"/></svg>9471 2658</p><p class="web">www.portalsdrapesandlouvres.com.au</p></div>
    <div class="photo photo--plantation" role="img" aria-label="Photo of white plantation shutters with a pendant light"></div>
    <h2 class="product product--small">Plantation<br>Shutters</h2>
    <svg class="badge" role="img" aria-label="Celebrating 13 years in business"><use href="#anniversary-badge"/></svg>
    <div class="offer"><span class="offer__top">FROM</span><span class="offer__value"><span class="offer__cur">$</span><span class="offer__num">299</span><span class="offer__per">/sqm</span></span></div>
    <ul class="benefits"><li>Modern &amp; elegant</li><li>Light &amp; privacy control</li><li>Durable &amp; easy care</li></ul>
  </article>
  <article class="ad ad--story">
    <div class="brand"><span class="brand__mark"></span><span class="brand__name">Portals Drapes &amp; Louvres</span></div>
    <p class="sale"><span class="sale__big">SALE</span><span class="sale__small">NOW ON</span></p>
    <p class="address"><span class="address__label">Showroom address</span><span class="address__text">482 Upper Wattleby Road, Kestrel Heights</span></p>
    <div class="cta-band">BOOK A FREE QUOTE TODAY!</div>
    <div class="contact-band"><p class="phone"><svg><use href="#phone-icon"/></svg>9471 2658</p><p class="web">www.portalsdrapesandlouvres.com.au</p></div>
    <div class="photo photo--plantation" role="img" aria-label="Photo of white plantation shutters with a pendant light"></div>
    <h2 class="product product--small">Plantation<br>Shutters</h2>
    <div class="offer"><span class="offer__top">FROM</span><span class="offer__value"><span class="offer__cur">$</span><span class="offer__num">299</span><span class="offer__per">/sqm</span></span></div>
    <ul class="benefits"><li>Modern &amp; elegant</li><li>Light &amp; privacy control</li><li>Durable &amp; easy care</li></ul>
    <svg class="badge" role="img" aria-label="Celebrating 13 years in business"><use href="#anniversary-badge"/></svg>
  </article>
  <article class="ad ad--square">
    <p class="sale"><span>SALE NOW ON</span></p>
    <div class="brand"><span class="brand__mark"></span><span class="brand__name">Portals Drapes &amp; Louvres</span></div>
    <p class="address"><span class="address__label">Showroom address</span><span class="address__text">482 Upper Wattleby Road, Kestrel Heights</span></p>
    <div class="cta-band">BOOK A FREE QUOTE TODAY!</div>
    <div class="contact-band"><p class="phone"><svg><use href="#phone-icon"/></svg>9471 2658</p><p class="web">www.portalsdrapesandlouvres.com.au</p></div>
    <div class="photo photo--plantation" role="img" aria-label="Photo of white plantation shutters with a pendant light"></div>
    <h2 class="product product--small">Plantation<br>Shutters</h2>
    <svg class="badge" role="img" aria-label="Celebrating 13 years in business"><use href="#anniversary-badge"/></svg>
    <div class="offer"><span class="offer__top">FROM</span><span class="offer__value"><span class="offer__cur">$</span><span class="offer__num">299</span><span class="offer__per">/sqm</span></span></div>
    <ul class="benefits"><li>Modern &amp; elegant</li><li>Light &amp; privacy control</li><li>Durable &amp; easy care</li></ul>
  </article>
  <span class="size-label size-label--feed">1440 X 1800</span>
  <span class="size-label size-label--story">1080 X 1920</span>
  <span class="size-label size-label--square">1080 X 1080</span>
</section>

</main>
</body>
</html>
```